Computer Service Provider in Need of New Letterhead Design

We are BrackenLoop Computer Services, a computer/IT services company that provides IT Support, software, hardware, virus monitoring, etc. in Vermont. We are looking for new letterhead, that is both professional and matches the current theme of our business cards & website.
Please note that we want to include the following information:
www.BrackenLoop.example
802-471-3926
742 Hollis Meadow Lane, Fernhollow, VT 05990
Steady Support • Friendly Experts • Reliable Results
I will be attaching our logo along with the business card images.
We would love to have the

```html
<!DOCTYPE html>
<html lang="en">
<head>
<meta charset="utf-8">
<title>BrackenLoop Computer Services – Letterhead</title>
<link rel="stylesheet" href="https://fonts.googleapis.com/css2?family=Roboto:wght@400;500;700&display=swap">
<style>
  :root {
    --brand-blue: #245a8c;
    --ink: #3a3a3a;
    --ink-dark: #222;
    --paper: #fbfbfb;
    --backdrop: #e4e6e8;
    --rule: #245a8c;
  }
  * { box-sizing: border-box; margin: 0; padding: 0; }
  html, body { width: 1200px; height: 1200px; overflow: hidden; }
  body {
    background: var(--backdrop);
    font-family: "Roboto", Arial, sans-serif;
    color: var(--ink);
  }
  .letterhead {
    position: absolute;
    left: 185px; top: 30px;
    width: 830px; height: 1140px;
    background: var(--paper);
    box-shadow: 0 2px 12px rgba(0,0,0,.12);
  }
  .brand {
    position: absolute; left: 84px; top: 60px;
    display: flex; align-items: center; gap: 12px;
  }
  .brand-square { width: 58px; height: 58px; background: var(--brand-blue); }
  .brand-name {
    font-weight: 700; font-size: 26px; color: var(--brand-blue);
    letter-spacing: .2px;
  }
  .contact {
    position: absolute; left: 566px; top: 62px;
    list-style: none; font-size: 13.5px; color: var(--ink-dark); line-height: 16.5px;
  }
  .contact li { display: flex; align-items: center; gap: 6px; }
  .contact svg { width: 10px; height: 10px; fill: none; stroke: var(--ink); stroke-width: 1.3; }
  .letter {
    position: absolute; left: 84px; top: 272px; width: 662px;
    font-size: 13.4px; line-height: 16.6px;
  }
  .letter-date { margin-bottom: 32px; }
  .letter-greeting { font-weight: 500; color: var(--ink-dark); margin-bottom: 16px; }
  .letter p.body { text-align: justify; margin-bottom: 17px; }
  .signoff { margin-top: 24px; }
  .signature {
    display: block; width: 176px; height: 26px; margin: 12px 0 4px;
    background: linear-gradient(90deg, #d9d9d9, #cfcfcf);
    border-radius: 3px;
  }
  .signer-title { display: block; }
  .signer-company { display: block; font-weight: 700; color: var(--ink-dark); }
  .footer {
    position: absolute; left: 83px; right: 84px; top: 1086px;
    font-size: 13.4px; line-height: 17px; color: var(--ink-dark);
  }
  .footer-address { display: block; padding-bottom: 5px; }
  .footer-address strong { color: var(--brand-blue); font-weight: 700; }
  .footer-rule {
    position: absolute; left: 0; right: 28px; top: 20px;
    border-top: 1.5px solid var(--rule);
  }
  .footer-square {
    position: absolute; right: 0; top: 8px;
    width: 28px; height: 28px; background: var(--brand-blue);
  }
  .footer-tagline { display: block; padding-top: 3px; }
</style>
</head>
<body>
  <main class="letterhead">
    <header>
      <div class="brand">
        <span class="brand-square" aria-hidden="true"></span>
        <span class="brand-name">BrackenLoop</span>
      </div>
      <ul class="contact">
        <li><svg viewBox="0 0 10 10"><path d="M2 1l2 2-1 1.3c.6 1.2 1.5 2.1 2.7 2.7L7 6l2 2-1.3 1.3C4.5 9 1 5.5.7 2.3z"/></svg>802-471-3926</li>
        <li><svg viewBox="0 0 10 10"><rect x="1" y="2" width="8" height="6"/><path d="M1 2l4 3.3L9 2"/></svg>info@BrackenLoop.example</li>
        <li><svg viewBox="0 0 10 10"><circle cx="5" cy="5" r="4"/><path d="M1 5h8M5 1c-2 2.4-2 5.6 0 8M5 1c2 2.4 2 5.6 0 8"/></svg>www.BrackenLoop.example</li>
      </ul>
    </header>

    <section class="letter">
      <p class="letter-date">January 01, 2020</p>
      <p class="letter-greeting">Dear Daniel Whitcomb,</p>
      <p class="body">Lorem ipsum dolor sit amet, consectetuer adipiscing elit, sed diam nonummy nibh euismod tincidunt ut laoreet dolore magna aliquam erat volutpat. Ut wisi enim ad minim veniam, quis nostrud exerci tation ullamcorper suscipit lobortis nisl ut aliquip ex ea commodo consequat. Duis dolore te feugait nulla facilisi. Nam liber tempor cum soluta nobis eleifend option congue nihil imperdiet doming id quod mazim placerat facer possim assum. Duis autem vel eum iriure dolor in hendrerit in vulputate velit esse molestie consequat, vel illum dolore eu feugiat nulla facilisis at vero eros et accumsan et iusto odio dignissim qui blandit praesent luptatum zzril delenit augue duis dolore te feugait nulla facilisi. Consectetuer adipiscing elit, sed diam nonummy nibh euismod tincidunt ut laoreet dolore magna aliquam erat volutpat. Ut wisi enim ad minim veniam, quis nostrud exerci tation ullamcorper suscipit lobortis nisl ut aliquip ex ea commodo consequat.</p>
      <p class="body">Consectetuer adipiscing elit, sed diam nonummy nibh euismod tincidunt ut laoreet dolore magna aliquam erat volutpat. Ut wisi enim ad minim veniam, quis nostrud exerci tation ullamcorper suscipit lobortis nisl ut aliquip ex ea commodo consequat. Consectetuer adipiscing elit, sed diam nonummy nibh euismod tincidunt ut laoreet dolore magna aliquam erat volutpat. Ut wisi enim ad minim veniam, quis nostrud exerci tation ullamcorper suscipit lobortis nisl ut aliquip ex ea commodo consequat.</p>
      <p class="body">Dolor sit amet, consectetuer adipiscing elit, sed diam nonummy nibh euismod tincidunt ut laoreet dolore magna aliquam erat volutpat. Ut wisi enim ad minim veniam, quis nostrud exerci tation ullamcorper suscipit lobortis nisl ut aliquip ex ea commodo consequat. Duis dolore te feugait nulla facilisi. Nam liber tempor cum soluta nobis eleifend option congue nihil imperdiet doming id quod mazim placerat facer possim assum. Duis dolore te feugait nulla facilisi. Nam liber tempor cum soluta nobis eleifend option congue nihil imperdiet doming id quod mazim placerat facer possim assum. Duis dolore te feugait nulla facilisi. Nam liber tempor cum soluta nobis eleifend option congue nihil imperdiet doming id quod mazim placerat facer possim assum.</p>
      <div class="signoff">
        <p>Sincerely Yours,</p>
        <span class="signature" role="img" aria-label="Handwritten signature of Owen Marsh"></span>
        <span class="signer-title">Authorized Managing Director</span>
        <span class="signer-company">Your Company Name</span>
      </div>
    </section>

    <footer class="footer">
      <span class="footer-address"><strong>BrackenLoop Computer Services</strong>, 742 Hollis Meadow Lane, Fernhollow, VT 05990</span>
      <span class="footer-rule" aria-hidden="true"></span>
      <span class="footer-square" aria-hidden="true"></span>
      <span class="footer-tagline">Steady Support • Friendly Experts • Reliable Results</span>
    </footer>
  </main>
</body>
</html>
```